Clear Plastic Card Design

I am looking to have a business card designed from my logo icon. I am looking to match the style of a different business card I have attached in the files.
Looking for a card that is plastic, with layers of transparency in the shape of my logo icon (also attached in the files) - not a circle like the other card. The winning design will incorporate the red icon logo on the front and back and include the charity's name, "Light for the Weary Souls" in the same or similar font, as well as an email and phone number. For now, use the email: email@lightfortheweary-mail.org and the phone number 555-382-7194.
We like how the sample business card has transparency, partial and full opacity layers and a matching color scheme. Files will need to be in vector so that our business card printing company can work with it.
UPDATE:
We've some excellent designs in, thank you everyone! I got an early review from the owner, and he requested a minor redirect to find his perfect design. He wants the design to stand out by NOT being a rectangle. Try instead a circle, square, or best yet - something that falls in the outline of the logo icon, either fully or partially. Thank you, everyone!
Light for the Weary Souls text should be incorporated as well as a phone and email.

```html
<!DOCTYPE html>
<html lang="en">
<head>
<meta charset="UTF-8">
<title>Light for the Weary Souls – Business Card</title>
<link href="https://fonts.googleapis.com/css2?family=Questrial&family=Arimo:wght@400&display=swap" rel="stylesheet">
<style>
  :root {
    --page-bg: #e6e6e6;
    --card-bg: #ffffff;
    --brand-red: #d8261e;
    --brand-orange: #ee5a1c;
    --ink: #111111;
  }
  * { box-sizing: border-box; margin: 0; padding: 0; }
  html, body {
    width: 1175px;
    height: 1200px;
    overflow: hidden;
    background: var(--page-bg);
  }
  .card {
    position: absolute;
    left: 87px;
    top: 100px;
    width: 1000px;
    height: 1000px;
    background: var(--card-bg);
    border-radius: 56px;
  }
  .brand-square {
    position: absolute;
    left: 390px;
    top: 150px;
    width: 250px;
    height: 250px;
    background: var(--brand-orange);
  }
  .brand-name {
    position: absolute;
    left: 67px;
    top: 415px;
    font-family: "Questrial", sans-serif;
    font-size: 54px;
    line-height: 1.12;
    color: var(--brand-red);
    font-weight: 400;
  }
  .contact-list {
    position: absolute;
    left: 67px;
    top: 700px;
    list-style: none;
    font-family: "Arimo", sans-serif;
    font-size: 39px;
    color: var(--ink);
  }
  .contact-item {
    display: flex;
    align-items: center;
    height: 58px;
  }
  .contact-icon {
    width: 34px;
    height: 34px;
    margin-right: 24px;
    fill: var(--ink);
    flex: none;
  }
</style>
</head>
<body>
  <main class="card">
    <div class="brand-square"></div>
    <h1 class="brand-name">Light for the<br>Weary Souls</h1>

    <ul class="contact-list">
      <li class="contact-item">
        <svg class="contact-icon" viewBox="0 0 24 24" aria-hidden="true">
          <path d="M6.6 10.8c1.4 2.8 3.8 5.1 6.6 6.6l2.2-2.2c.3-.3.7-.4 1-.2 1.1.4 2.3.6 3.6.6.6 0 1 .4 1 1V20c0 .6-.4 1-1 1C10.6 21 3 13.4 3 4c0-.6.4-1 1-1h3.5c.6 0 1 .4 1 1 0 1.3.2 2.5.6 3.6.1.3 0 .7-.2 1z"/>
        </svg>
        <span class="contact-text">555-382-7194</span>
      </li>
      <li class="contact-item">
        <svg class="contact-icon" viewBox="0 0 24 24" aria-hidden="true">
          <path d="M2 5h20v2l-10 6L2 7z"/>
          <path d="M2 9l10 6 10-6v10H2z"/>
        </svg>
        <span class="contact-text">email@lightfortheweary-mail.org</span>
      </li>
      <li class="contact-item">
        <svg class="contact-icon" viewBox="0 0 24 24" aria-hidden="true">
          <circle cx="12" cy="12" r="10"/>
          <path d="M12 3a9 9 0 0 0-7.5 4l2.5 1 1 3 2 1v3l2 2V13l2-1 1-3h2l1-2a9 9 0 0 0-6-4z" fill="#ffffff"/>
          <path d="M15 15l2 1v3a9 9 0 0 1-3 1.5z" fill="#ffffff"/>
        </svg>
        <span class="contact-text">www.lightfortheweary-souls.org</span>
      </li>
    </ul>
  </main>
</body>
</html>
```